Corvane Paintless Dent Removal

Our company works on vehicles removing dents using a highly skilled trade which the metal is massaged out with special tools without disturbing the original paint, hence paintless dent removal. Besides keeping the paint and metal original its also very environmentally friendly since no paint or toxic fillers are used. Also we we are one of the most experienced companies in the business with 25 years

Target Market(s)

Retail Automobile consumers, Auto Dealerships and Auto Body Shops

Industry/Entity Type

Auto Repair

Contact Information for Business Card

Dale Hollister
PO Box 518 Brookmere, NY 11962
631-555-0148
corvanepdr@mailbox-example.com
website corvanepdr.example
youtube corvane paintless dent removal
25 years of experience removing Dents, Dings and Hail Damage

Font styles to use
Serif
Sans Serif

Colors

Designer to choose colors to be used in the design.

Requirements
Must have
• I do like things that are simple but classy and somewhat bold, also I like my logo so that should be somewhat important

```html
<!DOCTYPE html>
<html lang="en">
<head>
<meta charset="utf-8">
<title>Corvane Paintless Dent Removal – Business Card</title>
<link href="https://fonts.googleapis.com/css2?family=Mulish:wght@700;800&family=Roboto:wght@400&display=swap" rel="stylesheet">
<style>
  :root {
    --navy: #0f2748;
    --lime: #7cc22a;
    --paper: #f4f4f4;
    --ink: #3c3c3c;
    --backdrop: #e6e3df;
    --gold: #d6a23a;
    --badge-dark: #1a1a1a;
    --white: #ffffff;
  }
  * { margin: 0; padding: 0; box-sizing: border-box; }
  html, body { width: 1200px; height: 960px; overflow: hidden; }
  body { background: var(--backdrop); position: relative; font-family: 'Roboto', Arial, sans-serif; }

  .card { position: absolute; }
  .card-front { left: 314px; top: 113px; width: 628px; height: 343px; background: var(--paper); }
  .card-back { left: 311px; top: 472px; width: 600px; height: 343px; background: var(--navy); }

  .brand-name {
    position: absolute;
    font-family: 'Mulish', Arial, sans-serif;
    font-weight: 800;
    text-align: center;
    line-height: 1.05;
  }
  .brand-name .brand-word { display: block; font-size: 34px; letter-spacing: 0.5px; }
  .brand-name .brand-tag { display: block; font-size: 15px; }
  .card-front .brand-name { left: 281px; top: 48px; width: 278px; color: var(--navy); }
  .card-back .brand-name { left: 124px; top: 124px; width: 340px; color: var(--white); }
  .card-back .brand-name .brand-word { font-size: 42px; }
  .card-back .brand-name .brand-tag { font-size: 18px; }

  .name-marker { position: absolute; left: 0; top: 192px; width: 14px; height: 25px; background: var(--navy); }
  .holder-name {
    position: absolute; left: 40px; top: 193px;
    font-family: 'Mulish', Arial, sans-serif; font-weight: 800;
    font-size: 21px; color: var(--navy); letter-spacing: 0.3px; text-transform: uppercase;
  }

  .contact-list { position: absolute; left: 41px; top: 235px; list-style: none; }
  .contact-list li {
    display: flex; align-items: center; height: 19.5px;
    font-size: 14px; color: var(--ink);
  }
  .contact-icon { width: 13px; height: 13px; margin-right: 9px; flex: none; }
  .contact-icon.plain-square { background: var(--navy); border-radius: 2px; width: 12px; height: 10px; }

  .divider { position: absolute; left: 297px; top: 277px; width: 1px; height: 30px; background: #8a8a8a; }
  .address { position: absolute; left: 313px; top: 274px; font-size: 14px; color: var(--ink); line-height: 18px; }

  .experience-badge { position: absolute; left: 493px; top: 250px; width: 70px; height: 70px; }

  .web-address {
    position: absolute; left: 0; width: 100%; top: 280px; text-align: center;
    color: var(--white); font-size: 14px; letter-spacing: 4.6px;
  }
</style>
</head>
<body>

<section class="card card-front" aria-label="Business card front">
  <div class="brand-name">
    <span class="brand-word">CORVANE</span>
    <span class="brand-tag">Paintless Dent Removal</span>
  </div>

  <div class="name-marker"></div>
  <h1 class="holder-name">Dale Hollister</h1>

  <ul class="contact-list">
    <li>
      <svg class="contact-icon" viewBox="0 0 24 24"><path fill="#0f2748" d="M6.6 10.8a15.1 15.1 0 0 0 6.6 6.6l2.2-2.2c.3-.3.7-.4 1-.2 1.1.4 2.3.6 3.6.6.6 0 1 .4 1 1V20c0 .6-.4 1-1 1A17 17 0 0 1 3 4c0-.6.4-1 1-1h3.5c.6 0 1 .4 1 1 0 1.3.2 2.5.6 3.6.1.3 0 .7-.2 1z"/></svg>
      631-555-0148
    </li>
    <li>
      <svg class="contact-icon" viewBox="0 0 24 24"><path fill="#0f2748" d="M2 5h20v14H2z"/><path fill="none" stroke="#f4f4f4" stroke-width="2" d="M3 6l9 7 9-7"/></svg>
      corvanepdr@mailbox-example.com
    </li>
    <li>
      <svg class="contact-icon" viewBox="0 0 24 24"><circle cx="12" cy="12" r="10" fill="#0f2748"/><path fill="none" stroke="#f4f4f4" stroke-width="1.6" d="M2 12h20M12 2c3 3 3 17 0 20M12 2c-3 3-3 17 0 20"/></svg>
      corvanepdr.example
    </li>
    <li>
      <span class="contact-icon plain-square"></span>
      corvane paintless dent removal
    </li>
  </ul>

  <div class="divider"></div>
  <p class="address">PO Box 518<br>Brookmere, NY 11962</p>

  <svg class="experience-badge" viewBox="0 0 70 70" role="img" aria-label="25 years of experience seal">
    <circle cx="35" cy="35" r="35" fill="var(--gold)"/>
    <circle cx="35" cy="35" r="24" fill="var(--badge-dark)"/>
  </svg>
</section>

<section class="card card-back" aria-label="Business card back">
  <div class="brand-name">
    <span class="brand-word">CORVANE</span>
    <span class="brand-tag">Paintless Dent Removal</span>
  </div>
  <p class="web-address">www.corvanepdr.example</p>
</section>

</body>
</html>
```